Law Firm Advertising Design Needed

Law Office of Dalmer K Quoss provides legal services to businesses and individuals who have been or are being injured. Our main practice area is personal injury (car accidents, wrongful death, premises liability), but we are looking for an ad that highlights a lesser known area of our practice - insurance company bad faith and breach of contract.

This ad will be placed in 8 1/2" x 11" format in a local neighborhood directory. It will also be placed in a smaller format (to be determined) in the local newspaper of a region of Arizona that has recently lost a considerable number of homes and people to wildfire.

We want to convey through the ad that our firm is available to help if their insurance company is not paying a legitimate claim or not paying enough for their claim.

Because of the tragic nature of the events in Velmont, we would like to avoid images of fire or anything resembling fire. However, the ad should capture the attention of individuals who are struggling through an insurance claim with all the stacks of paperwork and frustrated with unresponsive adjusters and unreasonably low offers.

The design should convey a feeling of safety, security and being taken care of.

Information that must be included in the ad are: the firm name (Law Office of Dalmer K Quoss), address (47390 N 18th Street, Ste 506, Phoenix, AZ 85044), the phone number (602-514-7730) and the fact that we have mobile offices available to assist in your area.

An example of text that has been used in the past is here:
"If your own insurance company is refusing to pay what you are owed on a claim, call the Law Office of Dalmer K Quoss. We fight for you by examining the reasons your insurance carrier is denying or making an insufficient offer on the claim; updating and correcting claim documentation; making a new demand and filing a lawsuit if necessary. Whether it's a simple misunderstanding or something more complicated, we can help!

Here are a few of the kinds of claims we handle:
- Hit and Run or Uninsured driver claims
- Fire, flood and property loss
- Life insurance benefits
- Health insurance claims
- Catastrophic losses
- Business insurance
- Wrongful Death Benefits

Our attorneys are available to help you cut through the nonsense. Call to make an appointment for a free consultation with an attorney today. "

An example of a previous ad for car accident services is attached for reference.
Updates

Hi Everyone,

The main lawyer involved in the decision making process has been giving me some feedback in general on the designs that I thought I would pass along.  He does not want the name of the law firm to be the first thing you notice when you look at the ad. Try to keep that small and possibly to the bottom of the ad. The phone number should be rather large, but the address should be rather small (we are required by the Lawyers' Guild to include our address, but we don't want our location to limit the location of our clients because our mobile offices can travel to them).  He would prefer that the logo either not be included or be not a significant part of the ad.

                                   

Thanks!  I will continue providing individual feedback to ads received. 

Target Market(s)

Low to middle income residents of the State of Arizona with little or no college education

Industry/Entity Type

Insurance

```html
<!DOCTYPE html>
<html lang="en">
<head>
<meta charset="utf-8">
<title>We Fight For You – Law Office of Dalmer K Quoss</title>
<link href="https://fonts.googleapis.com/css2?family=Cinzel:wght@700&family=Crimson+Text:ital,wght@0,400;0,600;0,700;1,400;1,600;1,700&display=swap" rel="stylesheet">
<style>
  :root {
    --page-bg: #ececec;
    --band-teal: #1d5670;
    --band-teal-dark: #154459;
    --body-navy: #1c3b53;
    --body-navy-deep: #162d40;
    --footer-navy: #172a3c;
    --text-white: #ffffff;
    --text-soft: #e3eaf0;
    --tick-green: #8fd13a;
    --photo-light: #b9c9da;
    --photo-mid: #7f98b3;
    --photo-skin: #c9a58e;
  }
  * { margin: 0; padding: 0; box-sizing: border-box; }
  html, body { width: 1200px; height: 1000px; overflow: hidden; }
  body {
    background: var(--page-bg);
    font-family: "Crimson Text", Georgia, serif;
    color: var(--text-white);
    position: relative;
  }
  .flyer {
    position: absolute;
    left: 296px; top: 105px;
    width: 612px; height: 790px;
    background: linear-gradient(180deg, var(--body-navy) 0%, var(--body-navy-deep) 100%);
    overflow: hidden;
  }
  .headline-band {
    position: absolute; left: 0; top: 0; width: 100%; height: 80px;
    background: linear-gradient(180deg, var(--band-teal) 0%, var(--band-teal-dark) 100%);
    box-shadow: 0 3px 6px rgba(0,0,0,.35);
  }
  .headline {
    font-family: "Cinzel", "Times New Roman", serif;
    font-weight: 700;
    font-size: 53px;
    line-height: 80px;
    text-align: center;
    letter-spacing: 0.5px;
    white-space: nowrap;
  }
  .intro {
    position: absolute; left: 23px; top: 88px; width: 564px;
    font-size: 15.2px; line-height: 19.2px;
    text-align: justify;
    color: var(--text-soft);
  }
  .intro strong { font-weight: 700; color: var(--text-white); }
  .intro .cta-inline { font-weight: 700; color: var(--text-white); }
  .availability {
    position: absolute; left: 25px; top: 215px;
    font-size: 15.5px; font-style: italic; color: var(--text-soft);
  }
  .availability strong { font-weight: 700; letter-spacing: 0.6px; }
  .claims {
    position: absolute; top: 243px; list-style: none;
    font-size: 15.2px; line-height: 18px; color: var(--text-soft);
  }
  .claims--left { left: 32px; }
  .claims--right { left: 362px; }
  .claims li { padding-left: 18px; position: relative; }
  .claims li.tick::before {
    content: "✓"; position: absolute; left: 0; top: 0;
    color: var(--tick-green); font-weight: 700;
  }
  .claims li.more { font-style: italic; }
  .appointment-band {
    position: absolute; left: 0; top: 332px; width: 100%; height: 80px;
    background: linear-gradient(180deg, var(--band-teal) 0%, var(--band-teal-dark) 100%);
    box-shadow: 0 -2px 5px rgba(0,0,0,.3), 0 3px 6px rgba(0,0,0,.35);
    text-align: center;
  }
  .appointment-title {
    font-weight: 700; font-size: 32px; letter-spacing: 0.5px;
    padding-top: 8px; line-height: 38px; white-space: nowrap;
  }
  .appointment-sub {
    font-size: 18px; font-style: italic; font-weight: 600; line-height: 20px;
  }
  .appointment-sub strong { font-style: normal; font-weight: 700; letter-spacing: 0.3px; }
  .photo {
    position: absolute; left: 0; top: 414px; width: 100%; height: 232px;
    background: linear-gradient(120deg, var(--photo-light) 0%, var(--photo-mid) 45%, var(--photo-skin) 70%, var(--photo-light) 100%);
  }
  .firm-band {
    position: absolute; left: 0; top: 647px; width: 100%; height: 45px;
    background: linear-gradient(180deg, var(--band-teal) 0%, var(--band-teal-dark) 100%);
    box-shadow: 0 3px 6px rgba(0,0,0,.35);
  }
  .firm-name {
    position: absolute; left: 18px; top: 0;
    font-weight: 700; font-size: 22px; line-height: 45px; letter-spacing: 0.6px;
    white-space: nowrap;
  }
  .brand-name {
    position: absolute; right: 30px; top: 0;
    font-weight: 700; font-size: 22px; line-height: 45px;
    white-space: nowrap;
  }
  .address {
    position: absolute; left: 18px; top: 703px;
    font-size: 12px; color: var(--text-soft); white-space: nowrap;
  }
  .phone-line {
    position: absolute; left: 17px; top: 722px;
    font-weight: 700; font-size: 28px; letter-spacing: 0.8px; white-space: nowrap;
  }
  .mobile-note {
    position: absolute; left: 19px; top: 761px;
    font-size: 13.5px; font-style: italic; color: var(--text-soft); white-space: nowrap;
  }
  .website {
    position: absolute; right: 46px; top: 762px;
    font-family: Arial, Helvetica, sans-serif; font-size: 12px; color: var(--text-soft);
  }
</style>
</head>
<body>
  <article class="flyer">
    <header class="headline-band">
      <h1 class="headline">WE FIGHT FOR YOU</h1>
    </header>

    <p class="intro">If your own insurance company is refusing to pay what you are owed on a claim, call the Law Office of Dalmer K Quoss. <strong>We fight for you</strong> by examining the reasons your insurance carrier is denying or making an insufficient offer on the claim; updating and correcting claim documentation; making a new demand and filing a lawsuit if necessary. Whether it's a simple misunderstanding or something more complicated, <span class="cta-inline">WE CAN HELP!</span></p>

    <p class="availability"><strong>OUR ATTORNEYS ARE AVAILABLE</strong> to help you cut through the nonsense.</p>

    <ul class="claims claims--left">
      <li class="tick">Hit and Run or Uninsured driver claims</li>
      <li class="tick">Fire, flood and property loss</li>
      <li class="tick">Life insurance benefits</li>
      <li class="tick">Health insurance claims</li>
    </ul>
    <ul class="claims claims--right">
      <li class="tick">Catastrophic losses</li>
      <li class="tick">Business insurance</li>
      <li class="tick">Wrongful Death Benefits</li>
      <li class="more">and many more</li>
    </ul>

    <section class="appointment-band">
      <h2 class="appointment-title">CALL TO MAKE AN APPOINTMENT</h2>
      <p class="appointment-sub">for <strong>A FREE CONSULTATION</strong> with an attorney today!</p>
    </section>

    <div class="photo" role="img" aria-label="Close-up of a man in a light blue shirt holding a smartphone and tapping the screen"></div>

    <div class="firm-band">
      <p class="firm-name">LAW OFFICE OF DALMER K QUOSS</p>
      <p class="brand-name">Quoss Law</p>
    </div>

    <p class="address">Law Office of Dalmer K Quoss | 47390 N 18th Street, Ste 506, Phoenix, AZ 85044</p>
    <p class="phone-line">CALL US NOW!&nbsp; 602-514-7730</p>
    <p class="mobile-note">We have mobile offices available to assist in your area.</p>
    <p class="website">www.quosslaw.com</p>
  </article>
</body>
</html>
```